Brovanek Data Yellow rose letterhead

I have a new logo for my company but in its current form it is too large to be used on letterhead or as a email signature. I need to have the designer use elements from the current logo and create something close to the original but more suited for smaller items.
Updates

I just uploaded a copy of our logo that does not have the weathered affect. Thanks

Reason: More time for revisions

Industry/Entity Type

It Company

Requirements
Must have
• The design must maintain the visual effect of the current logo. It needs to include the yellow rose and the name of the company.
Nice to have
• It would be nice to maintain the stamp theme and incorporate my name, address, phone, email. etc.

```html
<!DOCTYPE html>
<html lang="en">
<head>
<meta charset="utf-8">
<title>Brovanek Data Letterhead</title>
<link href="https://fonts.googleapis.com/css2?family=Carlito:ital,wght@0,400;0,700;1,400&display=swap" rel="stylesheet">
<style>
  :root {
    --paper: #ffffff;
    --ink-grey: #9b9b9b;
    --rule-grey: #c9c9c9;
    --band-brown: #5a4a3e;
    --band-edge: #8a7a6c;
    --rose-yellow: #e9cf3c;
    --logo-brown: #4d3d31;
    --band-text: #ffffff;
  }
  * { box-sizing: border-box; margin: 0; padding: 0; }
  html, body {
    width: 1200px; height: 402px; overflow: hidden; background: var(--paper);
  }
  .letterhead {
    position: relative; width: 1200px; height: 402px;
    background: var(--paper);
    font-family: "Carlito", "Calibri", sans-serif;
  }
  .brand-block {
    position: absolute; left: 0; top: 0; width: 352px; height: 322px;
    display: flex; align-items: center; justify-content: center; gap: 16px;
  }
  .brand-square {
    width: 34px; height: 34px; background: var(--rose-yellow);
  }
  .brand-name {
    font-size: 40px; font-weight: 700; color: var(--logo-brown);
    letter-spacing: 1px;
  }
  .column-rule {
    position: absolute; left: 353px; top: 0; width: 2px; height: 322px;
    background: var(--rule-grey);
  }
  .contact {
    position: absolute; left: 400px; top: 18px; color: var(--ink-grey);
    font-style: italic;
  }
  .contact-name {
    font-size: 38px; line-height: 44px; display: flex; align-items: center; gap: 14px;
  }
  .contact-name svg { margin-top: -6px; }
  .contact-address {
    margin-top: 8px; font-size: 29px; line-height: 35px;
  }
  .contact-email {
    margin-top: 36px; font-size: 29px; line-height: 37px;
  }
  .footer-band {
    position: absolute; left: 0; top: 322px; width: 1200px; height: 80px;
    background: var(--band-brown); border-top: 3px solid var(--band-edge);
    display: flex; align-items: center; color: var(--band-text);
  }
  .band-label {
    width: 353px; text-align: center; font-size: 25px; letter-spacing: 0.5px;
    text-transform: uppercase;
  }
  .band-rule {
    width: 2px; height: 80px; background: var(--band-edge);
  }
  .band-tagline {
    padding-left: 42px; font-size: 32px; font-weight: 700; white-space: nowrap;
  }
</style>
</head>
<body>
  <div class="letterhead">
    <div class="brand-block">
      <span class="brand-square"></span>
      <span class="brand-name">Brovanek Data</span>
    </div>
    <div class="column-rule"></div>

    <div class="contact">
      <p class="contact-name">Dr. Mara Quillen
        <svg width="30" height="20" viewBox="0 0 30 20" aria-hidden="true">
          <polygon points="0,4 18,0 30,12 10,20" fill="var(--rose-yellow)"/>
        </svg>
      </p>
      <p class="contact-address">
        218 NW Cedar Hollow Rd, Ste. 4100<br>
        Lakeview Falls, TX 76099<br>
        (800) 555-0147
      </p>
      <p class="contact-email">mara@brovanek-data.com</p>
    </div>

    <div class="footer-band">
      <div class="band-label">The Insight Builders</div>
      <div class="band-rule"></div>
      <div class="band-tagline">Shaping the Nation’s Most Precise Customer Insights</div>
    </div>
  </div>
</body>
</html>
```